The quiet harbor with an elephant incorporated in the background

Target Market(s)

Real estate

Industry/Entity Type

Real Estate

Contact Information for Business Card

On back on want my name & number
In front I want the business name, "the quiet harbor", below to say staging & design

Logo Text

The quiet harbor

Font styles to use
Serif

Colors
000000

Requirements
Must have
• I want an elephant behind the writing in gold transperant

```html
<!DOCTYPE html>
<html lang="en">
<head>
<meta charset="utf-8">
<title>The Quiet Harbor – Business Card</title>
<link rel="stylesheet" href="https://fonts.googleapis.com/css2?family=Bebas+Neue&family=Roboto:wght@400&family=Cinzel:wght@400&family=Quicksand:wght@400&display=swap">
<style>
  :root {
    --stage: #e9e7e3;
    --card-front: #ffffff;
    --card-back: #0a0a0a;
    --ink: #111111;
    --rule: #555555;
    --gold: #c9a54a;
    --subtitle: #e6e6e6;
    --elephant-tone: rgba(214, 196, 150, 0.45);
  }
  html, body {
    margin: 0;
    padding: 0;
    width: 1200px;
    height: 1200px;
    overflow: hidden;
    background: var(--stage);
  }
  .canvas {
    position: relative;
    width: 1200px;
    height: 1200px;
  }
  .card {
    position: absolute;
    left: 214px;
    width: 771px;
    height: 439px;
    overflow: hidden;
    box-shadow: 0 6px 18px rgba(0, 0, 0, 0.18);
  }
  .card--front {
    top: 151px;
    background: var(--card-front);
  }
  .card--back {
    top: 633px;
    background: var(--card-back);
  }
  .elephant-mark {
    position: absolute;
    left: 349px;
    top: 0;
    width: 420px;
    height: 434px;
    background: radial-gradient(ellipse 55% 50% at 50% 55%, var(--elephant-tone) 0%, rgba(214, 196, 150, 0.18) 60%, rgba(214, 196, 150, 0) 100%);
  }
  .holder {
    position: absolute;
    right: calc(771px - 351px);
    top: 186px;
    text-align: right;
    color: var(--ink);
  }
  .holder__name {
    margin: 0;
    font-family: "Bebas Neue", sans-serif;
    font-size: 46px;
    line-height: 1;
    letter-spacing: 0.5px;
    font-weight: 400;
  }
  .holder__title {
    margin: 6px 0 0;
    font-family: "Roboto", sans-serif;
    font-size: 20px;
    line-height: 1.2;
  }
  .divider {
    position: absolute;
    left: 388px;
    top: 186px;
    width: 1.5px;
    height: 72px;
    background: var(--rule);
  }
  .contact {
    position: absolute;
    left: 424px;
    top: 180px;
    margin: 0;
    padding: 0;
    list-style: none;
    font-family: "Roboto", sans-serif;
    font-size: 19px;
    color: var(--ink);
  }
  .contact__item {
    display: flex;
    align-items: center;
    height: 28px;
  }
  .contact__icon {
    width: 17px;
    height: 17px;
    margin-right: 7px;
    flex: none;
  }
  .brand {
    position: absolute;
    left: 0;
    right: 0;
    top: 170px;
    text-align: center;
  }
  .brand__name {
    margin: 0;
    font-family: "Cinzel", serif;
    font-weight: 400;
    font-size: 43px;
    letter-spacing: 2px;
    line-height: 1;
    color: var(--gold);
  }
  .brand__tagline {
    margin: 10px 0 0;
    font-family: "Quicksand", sans-serif;
    font-size: 25px;
    letter-spacing: 0.5px;
    color: var(--subtitle);
  }
</style>
</head>
<body>
<main class="canvas">
  <section class="card card--front">
    <div class="elephant-mark" role="img" aria-label="Faint gold elephant with raised trunk in the background"></div>
    <div class="holder">
      <h1 class="holder__name">DANIEL HARPER</h1>
      <p class="holder__title">President &amp; CEO</p>
    </div>
    <div class="divider"></div>
    <ul class="contact">
      <li class="contact__item">
        <svg class="contact__icon" viewBox="0 0 24 24" fill="none" stroke="currentColor" stroke-width="1.8" stroke-linejoin="round"><path d="M5 3h4l2 5-2.5 1.5a11 11 0 0 0 6 6L16 13l5 2v4a2 2 0 0 1-2 2A17 17 0 0 1 3 5a2 2 0 0 1 2-2z"/></svg>
        000-000-0000
      </li>
      <li class="contact__item">
        <svg class="contact__icon" viewBox="0 0 24 24" fill="none" stroke="currentColor" stroke-width="1.8"><rect x="2.5" y="5" width="19" height="14"/><path d="M2.5 5l9.5 8 9.5-8"/></svg>
        harper@harbor-staging.com
      </li>
      <li class="contact__item">
        <svg class="contact__icon" viewBox="0 0 24 24" fill="none" stroke="currentColor" stroke-width="1.8"><circle cx="12" cy="12" r="9.5"/><ellipse cx="12" cy="12" rx="4" ry="9.5"/><path d="M2.5 12h19M4 7h16M4 17h16"/></svg>
        www.harbor-staging.com
      </li>
    </ul>
  </section>

  <section class="card card--back">
    <div class="brand">
      <h2 class="brand__name">THE QUIET HARBOR</h2>
      <p class="brand__tagline">staging &amp; design</p>
    </div>
  </section>
</main>
</body>
</html>
```